Business cards to launch an education platform

Hi,
I am looking at having new business cards designed.
I am a startup, developing a web platform for schools and university, the education world. It's an online assessment system.
I would like a card that looks classy, and that is using the colors and the font of my logo.

I have attached:
1) my logo
2) A business card that I have designed quickly so you can have all the information required in the card, but I really don't like it.
3) The font that I am using (Lato Regular) to design my web platform
4) Some screenshots of my web platform so you can have a look at the style that I have.

Target Market(s)

Major market: Education system: Schools and university
Minor markets: Business in general

Industry/Entity Type

Business

Contact Information for Business Card

Clara Fenwick
Director

M: 0437 518 902
E: clara.fenwick@amberLoomSystems.com.au

Requirements
Must have
• The colors of my logo

```html
<!DOCTYPE html>
<html lang="en">
<head>
<meta charset="utf-8">
<title>Amber Loom Systems — Business Cards</title>
<link rel="stylesheet" href="https://fonts.googleapis.com/css2?family=Lato:wght@400;700&display=swap">
<style>
  :root {
    --backdrop: #eeeae3;
    --brand-deep: #0d5fa6;
    --brand-mid: #1f7fc4;
    --brand-glow: #3ea3dc;
    --brand-navy: #1c3f6e;
    --brand-sky: #29b5e8;
    --card-white: #ffffff;
    --shadow: rgba(40, 30, 15, 0.35);
  }
  html, body {
    margin: 0;
    padding: 0;
    width: 1189px;
    height: 1200px;
    overflow: hidden;
    background: var(--backdrop);
    font-family: "Lato", Arial, sans-serif;
  }
  .sheet {
    position: relative;
    width: 1189px;
    height: 1200px;
  }
  .card {
    position: absolute;
    left: 171px;
    width: 856px;
    height: 487px;
    overflow: hidden;
    box-shadow: 6px 8px 10px var(--shadow);
  }
  .card--front {
    top: 68px;
    background: radial-gradient(ellipse 60% 70% at 52% 45%, var(--brand-glow) 0%, var(--brand-mid) 55%, var(--brand-deep) 100%);
  }
  .card--back {
    top: 627px;
    background: var(--card-white);
  }
  .brand-mark {
    position: absolute;
    display: block;
  }
  .card--front .brand-mark {
    left: 200px;
    top: 172px;
    width: 128px;
    height: 128px;
    background: var(--card-white);
  }
  .card--back .brand-mark {
    left: 66px;
    top: 78px;
    width: 134px;
    height: 134px;
    background: var(--brand-navy);
  }
  .wordmark {
    position: absolute;
    margin: 0;
    font-weight: 400;
    line-height: 1;
  }
  .wordmark__primary,
  .wordmark__secondary {
    display: block;
  }
  .wordmark__primary {
    font-size: 47px;
    letter-spacing: 4px;
  }
  .wordmark__secondary {
    font-size: 33px;
    letter-spacing: 4px;
    margin-top: 6px;
  }
  .card--front .wordmark {
    left: 360px;
    top: 203px;
    color: var(--card-white);
  }
  .card--back .wordmark {
    left: 224px;
    top: 106px;
    color: var(--brand-navy);
  }
  .swoosh {
    position: absolute;
    inset: 0;
    width: 856px;
    height: 487px;
  }
  .swoosh__fill { fill: url(#swooshGradient); }
  .swoosh__accent { fill: var(--brand-sky); }
  .contact {
    position: absolute;
    right: 33px;
    top: 304px;
    text-align: right;
    color: var(--card-white);
  }
  .contact__name {
    margin: 0;
    font-size: 33px;
    font-weight: 700;
    line-height: 1.05;
  }
  .contact__role {
    margin: 0;
    font-size: 21px;
    line-height: 1.2;
  }
  .contact__list {
    list-style: none;
    margin: 34px 0 0;
    padding: 0;
  }
  .contact__item {
    display: flex;
    justify-content: flex-end;
    align-items: center;
    gap: 12px;
    font-size: 21px;
    height: 30px;
  }
  .contact__icon {
    width: 24px;
    height: 24px;
    flex: none;
  }
</style>
</head>
<body>
<main class="sheet">
  <section class="card card--front" aria-label="Card front">
    <span class="brand-mark" aria-hidden="true"></span>
    <h1 class="wordmark">
      <span class="wordmark__primary">AMBER LOOM</span>
      <span class="wordmark__secondary">Systems</span>
    </h1>
  </section>

  <section class="card card--back" aria-label="Card back">
    <svg class="swoosh" viewBox="0 0 856 487" aria-hidden="true">
      <defs>
        <radialGradient id="swooshGradient" cx="0.75" cy="0.7" r="0.6">
          <stop offset="0" stop-color="#2a8fd0"/>
          <stop offset="1" stop-color="#0d5fa6"/>
        </radialGradient>
      </defs>
      <path class="swoosh__accent" d="M 104 487 Q 590 400 779 55 Q 620 410 150 487 Z"/>
      <path class="swoosh__fill" d="M 808 0 Q 660 400 172 487 L 856 487 L 856 0 Z"/>
    </svg>

    <span class="brand-mark" aria-hidden="true"></span>
    <h2 class="wordmark">
      <span class="wordmark__primary">AMBER LOOM</span>
      <span class="wordmark__secondary">Systems</span>
    </h2>

    <div class="contact">
      <p class="contact__name">Clara Fenwick</p>
      <p class="contact__role">Director</p>
      <ul class="contact__list">
        <li class="contact__item">
          <span>0437 518 902</span>
          <svg class="contact__icon" viewBox="0 0 24 24" aria-label="Mobile">
            <rect width="24" height="24" fill="#ffffff"/>
            <rect x="7" y="3" width="10" height="18" rx="1.5" fill="none" stroke="#0d5fa6" stroke-width="1.8"/>
            <rect x="9" y="6" width="6" height="5" fill="#0d5fa6"/>
            <circle cx="12" cy="17" r="1.2" fill="#0d5fa6"/>
          </svg>
        </li>
        <li class="contact__item">
          <span>clara.fenwick@amberLoomSystems.com.au</span>
          <svg class="contact__icon" viewBox="0 0 24 24" aria-label="Email">
            <rect width="24" height="24" fill="#ffffff"/>
            <rect x="4" y="6" width="16" height="12" fill="none" stroke="#0d5fa6" stroke-width="1.8"/>
            <path d="M 4 6 L 12 13 L 20 6 M 4 18 L 10 12 M 20 18 L 14 12" fill="none" stroke="#0d5fa6" stroke-width="1.6"/>
          </svg>
        </li>
      </ul>
    </div>
  </section>
</main>
</body>
</html>
```